Vexa - Booking activities for Kids and Adults.

The app allows booking of Kid's activities for a given date/time.
The app lists activities offered via various clubs (vendors) which a user can book for their kids.
The users can browse various clubs and their offered activities. The users can manage their kid's profiles.
Need a whole new look to the app. The existing app can be checked out at
https://apps.storefrontexample.test/details?id=com.vexakw
https://apps.appmarketexample.test/us/app/vexa-فيكسا/id7302958146?ls=1
Try using the app as Guest.

Target Market(s)

Kuwait

Font styles to use
Serif
Sans Serif

Requirements
Must have
• Home Screens
The home page should have everything from the existing app and a quick area to change between different kid's profile to see activities matching their interests ONLY. In the current version, there's no switch profile and hence we are showing the name tags on the activities.

We are also going to build ecommerce so we need that ecommerce look and feel.
Kindly maintain the image aspect ratio from the current app so the new version doesn't require new images.

Need a complete new innovative designs - Keep the color scheme same.
The designs should be minimalistic and image oriented. The design should be done in XD. The designs should be submitted in both light and dark theme.
Reference to be used - http://plimtor.example

D.M for more info if needed.

```html
<!DOCTYPE html>
<html lang="en">
<head>
<meta charset="utf-8">
<title>Vexa – App Screens</title>
<link rel="stylesheet" href="https://fonts.googleapis.com/css2?family=Fira+Sans:wght@400;500;600;700&family=Nunito:wght@400;600;800&display=swap">
<style>
  :root{
    --stage:#63b11f;
    --cyan:#00d3d8;
    --cyan-title:#12c7d6;
    --orange:#f5921e;
    --orange-text:#f08a1c;
    --white:#ffffff;
    --ink:#333333;
    --muted:#555555;
    --line:#e3e3e3;
    --panel:#f1f1f1;
    --send:#f4795a;
  }
  *{box-sizing:border-box;margin:0;padding:0}
  html,body{width:1200px;height:811px;overflow:hidden}
  body{background:var(--stage);font-family:"Fira Sans",sans-serif;position:relative}
  .screen{position:absolute;top:110px;width:283px;height:613px;border-radius:28px;overflow:hidden;background:var(--white)}
  .screen--login{left:104px}
  .screen--activities{left:460px}
  .screen--reviews{left:816px}
  .abs{position:absolute}

  /* login */
  .login-sky{position:absolute;inset:0;background:linear-gradient(180deg,#8fd0ef 0%,#c9e9f7 55%,#e6f5fb 75%)}
  .login-hills{position:absolute;left:0;right:0;bottom:0;height:148px;background:linear-gradient(180deg,#a7d93a 0%,#7cc22a 60%,#b8e23b 100%);border-radius:60% 60% 0 0/30% 30% 0 0}
  .brand-badge{position:absolute;left:78px;top:32px;width:128px;height:128px;border-radius:50%;background:var(--white);display:flex;align-items:center;justify-content:center;font-family:"Nunito",sans-serif;font-weight:600;font-size:38px;color:var(--orange)}
  .field{position:absolute;left:22px;width:241px;height:44px;background:var(--cyan);color:var(--white);font-family:"Nunito",sans-serif;font-size:13px;display:flex;align-items:center;padding-left:22px;border:1px solid #7fe9ec}
  .forgot{position:absolute;left:0;right:0;top:376px;text-align:center;font-family:"Nunito",sans-serif;font-size:13px;color:var(--ink)}
  .login-btn{position:absolute;left:22px;top:411px;width:241px;height:44px;background:var(--orange);color:var(--white);font-weight:700;font-size:14px;letter-spacing:.5px;display:flex;align-items:center;justify-content:center;box-shadow:0 2px 6px rgba(0,0,0,.15)}

  /* activities */
  .topbar-title{position:absolute;left:0;right:0;top:19px;text-align:center;font-size:19px;font-weight:700;color:var(--cyan-title)}
  .icon{position:absolute}
  .day{position:absolute;width:134px;height:61px;color:var(--white);text-align:center;display:flex;flex-direction:column;justify-content:center;gap:5px}
  .day--cyan{background:var(--cyan)}
  .day--orange{background:var(--orange)}
  .day__name{font-weight:600;font-size:12.5px}
  .day__date{font-size:11px}
  .date-band{position:absolute;left:4px;top:196px;width:271px;height:67px;background:var(--orange);border-radius:2px}
  .date-input{position:absolute;left:11px;top:13px;width:248px;height:42px;background:var(--white);border-radius:3px;font-size:11.5px;color:var(--muted);display:flex;align-items:center;justify-content:space-between;padding:0 12px 0 14px}
  .feed-bg{position:absolute;left:0;right:0;top:267px;bottom:0;background:var(--panel)}
  .tile{position:absolute;display:flex;align-items:flex-end;padding:0 0 18px 22px;color:var(--white);font-size:11.5px}
  .tile--big{left:4.5px;top:275px;width:270.5px;height:153px;background:linear-gradient(160deg,#7a9a3a,#4f7a26 55%,#9bb84a)}
  .tile--left{left:4.5px;top:434px;width:134px;height:123px;background:linear-gradient(160deg,#8a6a4a,#b8463a 60%,#5a4a3a);padding-left:18px;padding-bottom:18px}
  .tile--right{left:144px;top:434px;width:131px;height:123px;background:linear-gradient(160deg,#c98a5a,#9a7a6a 55%,#6a5a5a);padding-left:16px;padding-bottom:18px}
  .bottom-nav{position:absolute;left:0;right:0;bottom:0;height:38px;background:var(--orange);display:flex;justify-content:space-around;align-items:center;padding:0 18px}

  /* reviews */
  .review-title{position:absolute;left:0;right:0;top:20px;text-align:center;font-size:14px;font-weight:600;color:var(--orange-text);letter-spacing:.3px}
  .rule{position:absolute;left:20px;right:16px;height:1px;background:var(--line)}
  .review{position:absolute;left:20px;width:248px}
  .review__name{font-size:15px;color:var(--orange-text);line-height:18px}
  .review__meta{display:flex;justify-content:space-between;font-size:13px;color:var(--ink);margin-top:3px;line-height:18px}
  .review__meta time{font-size:11.5px;padding-right:6px}
  .review__body{font-size:13px;color:var(--muted);line-height:19px;margin-top:6px}
  .review__stars{margin-top:10px;display:flex;gap:2.5px}
  .compose{position:absolute;left:0;right:0;bottom:0;height:64px;background:var(--panel)}
  .compose__input{position:absolute;left:13px;top:19px;width:219px;height:30px;background:var(--white);border-radius:15px;border:1px solid #dcdcdc}
  .compose__send{position:absolute;left:241px;top:19px;width:30px;height:30px;border-radius:50%;background:var(--send);display:flex;align-items:center;justify-content:center}
</style>
</head>
<body>

<section class="screen screen--login" aria-label="Sign up screen">
  <div class="login-sky" role="img" aria-label="Illustrated sky with balloons, clouds and cartoon children on rockets"></div>
  <div class="login-hills" role="img" aria-label="Illustrated green hills with a group of cartoon children and trees"></div>
  <div class="brand-badge">Vexa</div>
  <div class="field" style="top:192px">User Name</div>
  <div class="field" style="top:252px">Email Address</div>
  <div class="field" style="top:310px">Password</div>
  <div class="forgot">Forgot Password?</div>
  <div class="login-btn">LOGIN</div>
</section>

<section class="screen screen--activities" aria-label="Kid's activities screen">
  <svg class="icon" style="left:14px;top:22px" width="18" height="16" viewBox="0 0 18 16"><path d="M16 8H3M8 2L2 8l6 6" fill="none" stroke="#222" stroke-width="2.4" stroke-linecap="round" stroke-linejoin="round"/></svg>
  <div class="topbar-title">Kid's activities</div>
  <svg class="icon" style="left:248px;top:22px" width="17" height="17" viewBox="0 0 17 17"><circle cx="7" cy="7" r="5.3" fill="none" stroke="#222" stroke-width="2.2"/><path d="M11 11l4.5 4.5" stroke="#222" stroke-width="2.4" stroke-linecap="round"/></svg>

  <div class="day day--cyan" style="left:4px;top:59px"><span class="day__name">TODAY</span><span class="day__date">Mon 7th August</span></div>
  <div class="day day--orange" style="left:142px;top:59px"><span class="day__name">TOMORROW</span><span class="day__date">Tue 8th August</span></div>
  <div class="day day--orange" style="left:4px;top:124px"><span class="day__name">SATURDAY</span><span class="day__date">13 h August</span></div>
  <div class="day day--cyan" style="left:142px;top:124px"><span class="day__name">SUNDAY</span><span class="day__date">Mon 7th August</span></div>

  <div class="feed-bg"></div>
  <div class="date-band">
    <div class="date-input">Pick a Date
      <svg width="11" height="11" viewBox="0 0 11 11"><rect x="1" y="2" width="9" height="8" rx="1" fill="none" stroke="#888" stroke-width="1"/><path d="M1 4.5h9M3.5 1v2M7.5 1v2" stroke="#888" stroke-width="1"/><path d="M3 6.5h1M5 6.5h1M7 6.5h1M3 8.3h1M5 8.3h1" stroke="#888" stroke-width="1"/></svg>
    </div>
  </div>

  <div class="tile tile--big" role="img" aria-label="Photo of children playing with a beach ball on grass">Nemo enim ipsam</div>
  <div class="tile tile--left" role="img" aria-label="Photo of a child at a playground">Nemo enim ipsam</div>
  <div class="tile tile--right" role="img" aria-label="Photo of children at a craft class">Nemo enim ipsam</div>

  <nav class="bottom-nav" aria-label="Main">
    <svg width="18" height="18" viewBox="0 0 18 18" aria-label="Home"><path d="M2 9l7-6 7 6M4 8v8h4v-5h2v5h4V8" fill="none" stroke="#fff" stroke-width="1.3" stroke-linejoin="round"/></svg>
    <svg width="18" height="18" viewBox="0 0 18 18" aria-label="Search"><circle cx="8" cy="8" r="6" fill="none" stroke="#fff" stroke-width="1.3"/><path d="M12.5 12.5l4 4" stroke="#fff" stroke-width="1.3"/></svg>
    <svg width="20" height="18" viewBox="0 0 20 18" aria-label="Camera"><rect x="2" y="4" width="16" height="11" rx="2" fill="none" stroke="#fff" stroke-width="1.3"/><circle cx="10" cy="9.5" r="3" fill="none" stroke="#fff" stroke-width="1.3"/><path d="M7 4l1.5-2h3L13 4" fill="none" stroke="#fff" stroke-width="1.3"/></svg>
    <svg width="18" height="18" viewBox="0 0 18 18" aria-label="Favourites"><path d="M9 15.5S2 11 2 6.5A3.5 3.5 0 0 1 9 5a3.5 3.5 0 0 1 7 1.5C16 11 9 15.5 9 15.5z" fill="none" stroke="#fff" stroke-width="1.3"/></svg>
    <svg width="18" height="18" viewBox="0 0 18 18" aria-label="Profile"><circle cx="9" cy="5.5" r="3.5" fill="none" stroke="#fff" stroke-width="1.3"/><path d="M2.5 16.5c0-3.5 3-5.5 6.5-5.5s6.5 2 6.5 5.5z" fill="none" stroke="#fff" stroke-width="1.3"/></svg>
  </nav>
</section>

<section class="screen screen--reviews" aria-label="Review screen">
  <svg class="icon" style="left:16px;top:20px" width="18" height="16" viewBox="0 0 18 16"><path d="M16 8H3M8 2L2 8l6 6" fill="none" stroke="#444" stroke-width="2.4" stroke-linecap="round" stroke-linejoin="round"/></svg>
  <div class="review-title">REVIEW</div>
  <svg class="icon" style="left:250px;top:20px" width="16" height="16" viewBox="0 0 17 17"><circle cx="7" cy="7" r="5.3" fill="none" stroke="#444" stroke-width="2.2"/><path d="M11 11l4.5 4.5" stroke="#444" stroke-width="2.4" stroke-linecap="round"/></svg>
  <div class="rule" style="top:54px"></div>

  <svg width="0" height="0" style="position:absolute"><defs><path id="star" d="M5.5 0l1.6 3.5 3.9.4-2.9 2.6.8 3.8-3.4-2-3.4 2 .8-3.8L0 3.9l3.9-.4z" fill="#f5921e"/></defs></svg>

  <article class="review" style="top:75px">
    <h3 class="review__name" style="font-weight:400">John Doe</h3>
    <p class="review__meta"><span>Nemo enim ipsam</span><time>OCT 17, 20</time></p>
    <p class="review__body">Sed ut perspiciatis unde omnis iste atus error sit voluptatem cusantium doloreue latium, totam</p>
    <div class="review__stars"><svg width="11" height="11"><use href="#star"/></svg><svg width="11" height="11"><use href="#star"/></svg><svg width="11" height="11"><use href="#star"/></svg><svg width="11" height="11"><use href="#star"/></svg><svg width="11" height="11"><use href="#star"/></svg></div>
  </article>
  <div class="rule" style="top:217px"></div>

  <article class="review" style="top:245px">
    <h3 class="review__name" style="font-weight:400">John Doe</h3>
    <p class="review__meta"><span>Nemo enim ipsam</span><time>OCT 17, 20</time></p>
    <p class="review__body">Sed ut perspiciatis unde omnis iste atus error sit voluptatem cusantium doloreue latium, totam</p>
    <div class="review__stars"><svg width="11" height="11"><use href="#star"/></svg><svg width="11" height="11"><use href="#star"/></svg><svg width="11" height="11"><use href="#star"/></svg><svg width="11" height="11"><use href="#star"/></svg><svg width="11" height="11"><use href="#star"/></svg></div>
  </article>
  <div class="rule" style="top:385px"></div>

  <article class="review" style="top:404px">
    <h3 class="review__name" style="font-weight:400">John Doe</h3>
    <p class="review__meta"><span>Nemo enim ipsam</span><time>OCT 17, 20</time></p>
    <p class="review__body">Sed ut perspiciatis unde omnis iste atus error sit voluptatem cusantium doloreue latium, totam</p>
    <div class="review__stars"><svg width="11" height="11"><use href="#star"/></svg><svg width="11" height="11"><use href="#star"/></svg><svg width="11" height="11"><use href="#star"/></svg><svg width="11" height="11"><use href="#star"/></svg><svg width="11" height="11"><use href="#star"/></svg></div>
  </article>

  <div class="compose">
    <div class="compose__input"></div>
    <div class="compose__send"><svg width="14" height="14" viewBox="0 0 14 14"><path d="M1 7.5L13 1 9.5 13 7 8.5z" fill="#fff"/></svg></div>
  </div>
</section>

</body>
</html>
```